Business card design

I need my logo on this card, things I need the card to have on it
licensed and insured.
owner operators Milo & Trent Halvorsen
my phone number 5083716254
Disaster Recovery, Storm Damage Restoration, Proactive Disaster Plan Management, Roof Repair/Restoration Structural Repair and Reconstruction, Emergency Boarding and Tarping Service, Perimeter Fencing, Emergency Tree Removal,

```html
<!DOCTYPE html>
<html lang="en">
<head>
<meta charset="utf-8">
<title>Halvorsen's Construction L.L.C — Business Card</title>
<link href="https://fonts.googleapis.com/css2?family=Lato:ital,wght@0,400;0,700;1,400&display=swap" rel="stylesheet">
<style>
  :root {
    --page-bg: #e9e7e4;
    --card-light: #f7f8f9;
    --card-mist: #e6e9ec;
    --brand-blue: #1f73c9;
    --brand-blue-light: #3d8ad8;
    --brand-blue-deep: #1561b5;
    --ink: #4a4f55;
    --white: #ffffff;
    --name-grey: #eef1f4;
  }
  * { box-sizing: border-box; margin: 0; padding: 0; }
  html, body {
    width: 1200px; height: 900px; overflow: hidden;
    background: var(--page-bg);
    font-family: "Lato", Arial, sans-serif;
  }
  .business-card {
    position: absolute; left: 97px; top: 162px;
    width: 1005px; height: 576px;
    border-radius: 24px; overflow: hidden;
    background: linear-gradient(135deg, var(--card-light) 0%, var(--card-mist) 100%);
    box-shadow: 0 10px 30px rgba(0,0,0,0.12);
  }
  .house-panel { position: absolute; inset: 0; width: 1005px; height: 576px; }

  .company-name {
    position: absolute; left: 52px; top: 196px;
    display: flex; align-items: center; gap: 14px;
    color: var(--brand-blue);
  }
  .name-square { width: 22px; height: 22px; background: var(--brand-blue); flex: none; }
  .name-lines { display: flex; flex-direction: column; }
  .name-main { font-weight: 400; font-size: 44px; letter-spacing: 1px; line-height: 1; }
  .name-sub { font-weight: 400; font-size: 15px; letter-spacing: 6.5px; line-height: 1; margin-top: 6px; }

  .service-list {
    position: absolute; left: 54px; top: 282px;
    list-style: none;
  }
  .service-list li {
    display: flex; align-items: center; gap: 12px;
    height: 31.5px;
    font-size: 20px; color: var(--ink);
  }
  .service-list svg { width: 19px; height: 19px; flex: none; }

  .owner-block {
    position: absolute; right: 62px; top: 128px;
    text-align: right; color: var(--white);
  }
  .owner-names {
    font-weight: 700; font-size: 56px; line-height: 1.32;
    color: var(--name-grey);
  }
  .owner-role { font-style: italic; font-size: 32px; line-height: 1.1; }
  .divider { width: 50px; height: 3px; background: var(--white); margin: 22px 0 18px auto; }
  .call-label { font-weight: 700; font-size: 28px; }
  .phone { font-weight: 700; font-size: 54px; letter-spacing: 1px; line-height: 1.1; }
  .credential { font-weight: 700; font-size: 28px; }
</style>
</head>
<body>
  <div class="business-card">
    <svg class="house-panel" viewBox="0 0 670 384" preserveAspectRatio="none" aria-hidden="true">
      <defs>
        <linearGradient id="houseFill" x1="0" y1="0" x2="1" y2="1">
          <stop offset="0" stop-color="#3d8ad8"/>
          <stop offset="1" stop-color="#1561b5"/>
        </linearGradient>
      </defs>
      <polygon fill="url(#houseFill)"
        points="260,214 356,127 356,64 396,64 396,90 495,0 670,0 670,384 356,384 356,214"/>
    </svg>

    <div class="company-name">
      <span class="name-square"></span>
      <span class="name-lines">
        <span class="name-main">HALVORSEN'S</span>
        <span class="name-sub">CONSTRUCTION L.L.C</span>
      </span>
    </div>

    <ul class="service-list">
      <li><svg viewBox="0 0 20 20"><circle cx="10" cy="10" r="10" fill="#2a78c6"/><path d="M5.5 10.3l3 3 6-6.3" fill="none" stroke="#fff" stroke-width="2.2"/></svg>Disaster Recovery</li>
      <li><svg viewBox="0 0 20 20"><circle cx="10" cy="10" r="10" fill="#2a78c6"/><path d="M5.5 10.3l3 3 6-6.3" fill="none" stroke="#fff" stroke-width="2.2"/></svg>Storm Damage Restoration</li>
      <li><svg viewBox="0 0 20 20"><circle cx="10" cy="10" r="10" fill="#2a78c6"/><path d="M5.5 10.3l3 3 6-6.3" fill="none" stroke="#fff" stroke-width="2.2"/></svg>Proactive Disaster Plan Management</li>
      <li><svg viewBox="0 0 20 20"><circle cx="10" cy="10" r="10" fill="#2a78c6"/><path d="M5.5 10.3l3 3 6-6.3" fill="none" stroke="#fff" stroke-width="2.2"/></svg>Roof Repair / Restoration</li>
      <li><svg viewBox="0 0 20 20"><circle cx="10" cy="10" r="10" fill="#2a78c6"/><path d="M5.5 10.3l3 3 6-6.3" fill="none" stroke="#fff" stroke-width="2.2"/></svg>Structural Repair &amp; Reconstruction</li>
      <li><svg viewBox="0 0 20 20"><circle cx="10" cy="10" r="10" fill="#2a78c6"/><path d="M5.5 10.3l3 3 6-6.3" fill="none" stroke="#fff" stroke-width="2.2"/></svg>Emergency Boarding &amp; Tarping Service</li>
      <li><svg viewBox="0 0 20 20"><circle cx="10" cy="10" r="10" fill="#2a78c6"/><path d="M5.5 10.3l3 3 6-6.3" fill="none" stroke="#fff" stroke-width="2.2"/></svg>Perimeter Fencing</li>
      <li><svg viewBox="0 0 20 20"><circle cx="10" cy="10" r="10" fill="#2a78c6"/><path d="M5.5 10.3l3 3 6-6.3" fill="none" stroke="#fff" stroke-width="2.2"/></svg>Emergency Tree Removal</li>
    </ul>

    <div class="owner-block">
      <p class="owner-names">MILO<br>&amp; TRENT</p>
      <p class="owner-role">Owner Operators</p>
      <div class="divider"></div>
      <p class="call-label">Call Us Today</p>
      <p class="phone">5083716254</p>
      <div class="divider"></div>
      <p class="credential">licensed &amp; insured</p>
    </div>
  </div>
</body>
</html>
```